Business Card Design Project for Heron Lending

Hello there,

We are looking for a business card design for our new Heron Lending car financing company. We are looking for a business card that will include:

- An address
- Telephone number and extension
- Employee Name
- Employee Title
- Our logo and name clearly visible

We are including our logo with this writeup, we are looking to convey friendliness, trus and memorability. Colors and everything else is up to you.

Target Market(s)

18-34 year old males and females

Industry/Entity Type

Business

```html
<!DOCTYPE html>
<html lang="en">
<head>
<meta charset="utf-8">
<title>Heron Lending — Business Card</title>
<link rel="stylesheet" href="https://fonts.googleapis.com/css2?family=Noto+Serif:wght@400;700&display=swap">
<style>
  :root {
    --navy: #223670;
    --ink: #1d1d1f;
    --paper: #ffffff;
    --backdrop: #e7e3dd;
    --rule: #2a2a2e;
  }
  * { box-sizing: border-box; margin: 0; padding: 0; }
  html, body {
    width: 1200px;
    height: 870px;
    overflow: hidden;
    background: var(--backdrop);
    font-family: "Noto Serif", Georgia, serif;
  }
  .sheet {
    position: relative;
    width: 1200px;
    height: 870px;
    display: flex;
    justify-content: center;
    align-items: center;
    gap: 80px;
  }
  .card {
    position: relative;
    width: 420px;
    height: 735px;
    background: var(--paper);
    box-shadow: 0 6px 18px rgba(0, 0, 0, 0.18);
    overflow: hidden;
  }
  .card__bands {
    position: absolute;
    left: 0;
    right: 0;
    bottom: 0;
    height: 66px;
  }
  .card__bands .band-thin {
    position: absolute;
    left: 0; right: 0; top: 0;
    height: 7px;
    background: var(--navy);
  }
  .card__bands .band-thick {
    position: absolute;
    left: 0; right: 0; bottom: 0;
    height: 46px;
    background: var(--navy);
  }
  .brand {
    position: absolute;
    left: 0;
    right: 0;
    text-align: center;
  }
  .brand__mark {
    display: block;
    width: 84px;
    height: 84px;
    margin: 0 auto 14px;
    border-radius: 50%;
    background: var(--navy);
  }
  .brand__rule {
    width: 270px;
    height: 3px;
    margin: 0 auto 14px;
    background: var(--rule);
  }
  .brand__name {
    color: var(--navy);
    font-weight: 400;
    font-size: 40px;
    letter-spacing: 3px;
    line-height: 1;
  }
  .card--front .brand { top: 58px; }
  .card--back .brand { top: 430px; }

  .contact {
    position: absolute;
    left: 0;
    right: 0;
    top: 320px;
    text-align: center;
    color: var(--ink);
  }
  .contact__name {
    color: var(--navy);
    font-weight: 700;
    font-size: 31px;
    line-height: 1.1;
  }
  .contact__title {
    font-size: 20px;
    line-height: 1.2;
  }
  .contact__phone {
    margin-top: 48px;
    font-size: 21px;
  }
  .contact__address {
    margin-top: 20px;
    font-size: 21px;
    line-height: 1.3;
    font-style: normal;
  }
</style>
</head>
<body>
<main class="sheet">
  <article class="card card--front">
    <div class="brand">
      <span class="brand__mark" aria-hidden="true"></span>
      <div class="brand__rule"></div>
      <div class="brand__name">Heron Lending</div>
    </div>
    <div class="contact">
      <p class="contact__name">Employee Name</p>
      <p class="contact__title">Project Manager</p>
      <p class="contact__phone">+1 (555) 0142 ext. 27</p>
      <address class="contact__address">
        48 Larkspur Rd., Millbrook,<br>
        NY 12608<br>
        P.O. Box: 570218
      </address>
    </div>
    <div class="card__bands">
      <div class="band-thin"></div>
      <div class="band-thick"></div>
    </div>
  </article>

  <article class="card card--back">
    <div class="brand">
      <span class="brand__mark" aria-hidden="true"></span>
      <div class="brand__rule"></div>
      <div class="brand__name">Heron Lending</div>
    </div>
    <div class="card__bands">
      <div class="band-thin"></div>
      <div class="band-thick"></div>
    </div>
  </article>
</main>
</body>
</html>
```